Velmora Freightway Solutions Business cards

Would like a very unique design catchy but professional for business cards. Please use log provided.Marlon WellsCeo and Founder TransCon Logistix Solutions1-888-913-3225mwells@tlsolutionsus.comwww.tlsolutionsus.com

```html
<!DOCTYPE html>
<html lang="en">
<head>
<meta charset="utf-8">
<title>Velmora Freightway Solutions – Business Cards</title>
<link href="https://fonts.googleapis.com/css2?family=Montserrat:wght@300;700&family=Open+Sans:wght@400;600&display=swap" rel="stylesheet">
<style>
  :root {
    --backdrop: #252527;
    --card: #151516;
    --card-edge: #202022;
    --blue: #3d8fd6;
    --blue-soft: #5a9bd5;
    --red: #e4545a;
    --white: #f4f4f4;
    --grey: #d8d8d8;
  }
  * { margin: 0; padding: 0; box-sizing: border-box; }
  html, body { width: 1200px; height: 900px; overflow: hidden; }
  body {
    background: var(--backdrop);
    font-family: "Open Sans", Arial, sans-serif;
    position: relative;
  }
  .card {
    position: absolute;
    left: 250px;
    width: 700px;
    height: 400px;
    background: var(--card);
    border: 1px solid var(--card-edge);
    border-radius: 26px;
  }
  .card--front { top: 40px; }
  .card--back { top: 470px; }

  .brand {
    display: flex;
    align-items: center;
    gap: 12px;
    position: absolute;
  }
  .brand__mark {
    width: 18px; height: 18px;
    background: var(--red);
    flex: none;
  }
  .brand__name {
    font-family: "Open Sans", Arial, sans-serif;
    font-weight: 600;
    color: var(--blue);
    letter-spacing: 1px;
    text-transform: uppercase;
    line-height: 1.15;
  }
  .card--front .brand {
    left: 0; right: 0; top: 170px;
    justify-content: center;
  }
  .card--front .brand__name { font-size: 30px; }

  .card--back .brand {
    left: 50px; top: 150px; width: 270px;
  }
  .card--back .brand__name { font-size: 21px; }

  .contact {
    position: absolute;
    left: 370px; top: 120px;
  }
  .contact__name {
    font-family: "Montserrat", Arial, sans-serif;
    font-size: 27px;
    color: var(--white);
    font-weight: 300;
    letter-spacing: 0.5px;
  }
  .contact__name strong { font-weight: 700; }
  .contact__title {
    font-size: 16px;
    color: var(--blue-soft);
    margin-top: 2px;
    letter-spacing: 0.3px;
  }
  .contact__list { list-style: none; margin-top: 26px; }
  .contact__item {
    display: flex; align-items: center; gap: 12px;
    font-size: 17px; color: var(--white);
    margin-bottom: 10px;
  }
  .contact__item svg { width: 15px; height: 15px; flex: none; }
  .address {
    position: absolute;
    left: 0; right: 0; bottom: 52px;
    text-align: center;
    font-size: 18px;
    color: var(--grey);
  }
</style>
</head>
<body>
  <section class="card card--front">
    <div class="brand">
      <span class="brand__mark"></span>
      <span class="brand__name">Velmora Freightway Solutions</span>
    </div>
  </section>

  <section class="card card--back">
    <div class="brand">
      <span class="brand__mark"></span>
      <span class="brand__name">Velmora Freightway Solutions</span>
    </div>

    <div class="contact">
      <h1 class="contact__name">DORIAN <strong>PIKE</strong></h1>
      <p class="contact__title">CEO AND FOUNDER</p>
      <ul class="contact__list">
        <li class="contact__item">
          <svg viewBox="0 0 16 16" aria-hidden="true"><path fill="#e4545a" d="M1 5c0-2 3-3 7-3s7 1 7 3v1h-4V5H5v1H1zM3 7h10l1 7H2zm5 2a2 2 0 1 0 0 4 2 2 0 0 0 0-4z"/></svg>
          1-888-470-6158
        </li>
        <li class="contact__item">
          <svg viewBox="0 0 16 16" aria-hidden="true"><rect x="1" y="3" width="14" height="10" fill="none" stroke="#e4545a" stroke-width="1.6"/><path d="M1 3l7 6 7-6" fill="none" stroke="#e4545a" stroke-width="1.6"/></svg>
          dpike@vfwayroutes.com
        </li>
        <li class="contact__item">
          <svg viewBox="0 0 16 16" aria-hidden="true"><g fill="none" stroke="#e4545a" stroke-width="1.3"><circle cx="8" cy="8" r="6.5"/><ellipse cx="8" cy="8" rx="3" ry="6.5"/><path d="M1.5 8h13M2.5 5h11M2.5 11h11"/></g></svg>
          www.vfwayroutes.com
        </li>
      </ul>
    </div>

    <p class="address">740 Harlow Creek Ave, Brenfield, GA 30482</p>
  </section>
</body>
</html>
```